Business Card Design Project

Basic business card with minimal details. I just need company name, email & web address, telephone and my name.
I would like the back of the card to be grey with my logo & company name centred.

Target Market(s)

Architects
Builders
Property Developers

Industry/Entity Type

Business

Font styles to use
Sans Serif

Colors

Designer to choose colors to be used in the design.

Requirements
Must have
• Tallow Crest
Rupert Hazelby - Director
M: 0427 915203
E: rupert@tallowcrest.com.au
W: www.tallowcrest.com.au
Should not have
• No other images or pictures

```html
<!DOCTYPE html>
<html lang="en">
<head>
<meta charset="utf-8">
<title>Tallow Crest – Business Card</title>
<link rel="stylesheet" href="https://fonts.googleapis.com/css2?family=Arimo:wght@400;700&display=swap">
<style>
  :root {
    --stage-light: #f4f4f4;
    --stage-dark: #dcdcdc;
    --card-grey: #c2c2c2;
    --brand-slate: #434b56;
    --brand-red: #9b1c33;
    --text-white: #ffffff;
    --icon-grey: #6f6f6f;
    --pattern-tone: #b4b4b4;
  }
  * { margin: 0; padding: 0; box-sizing: border-box; }
  html, body { width: 1200px; height: 999px; overflow: hidden; }
  body {
    position: relative;
    background: radial-gradient(ellipse at center, var(--stage-light) 0%, var(--stage-light) 45%, var(--stage-dark) 100%);
    font-family: "Arimo", Arial, sans-serif;
  }
  .card {
    position: absolute;
    top: 106px;
    width: 449px;
    height: 784px;
    background: var(--card-grey);
    overflow: hidden;
  }
  .card--back { left: 140px; }
  .card--front { left: 612px; }

  .brand {
    position: absolute;
    left: 0; right: 0;
    top: 258px;
    display: flex;
    flex-direction: column;
    align-items: center;
    gap: 58px;
  }
  .brand__square {
    width: 62px; height: 62px;
    background: var(--brand-red);
  }
  .brand__name {
    font-size: 40px;
    font-weight: 400;
    letter-spacing: 3px;
    color: var(--brand-slate);
    text-transform: uppercase;
    line-height: 1;
  }

  .pattern-field {
    position: absolute;
    left: 0; top: 110px;
    width: 449px; height: 674px;
    background: linear-gradient(135deg, rgba(180,180,180,0) 25%, rgba(180,180,180,0.55) 60%, rgba(172,172,172,0.75) 100%);
  }

  .holder {
    position: absolute;
    left: 19px; top: 76px;
    color: var(--text-white);
  }
  .holder__name {
    font-size: 33px;
    font-weight: 700;
    letter-spacing: 0.5px;
    line-height: 1;
    text-transform: uppercase;
  }
  .holder__title {
    font-size: 24px;
    font-weight: 400;
    margin-top: 6px;
    line-height: 1;
  }

  .contacts {
    position: absolute;
    left: 18px; top: 320px;
    list-style: none;
  }
  .contact {
    position: relative;
    height: 80px;
    display: flex;
    align-items: flex-start;
  }
  .contact__icon {
    width: 46px; height: 36px;
    flex: none;
    margin-right: 12px;
  }
  .contact__text {
    font-size: 25px;
    color: var(--text-white);
    line-height: 1;
    padding-top: 6px;
  }
</style>
</head>
<body>

<section class="card card--back">
  <div class="brand">
    <div class="brand__square"></div>
    <div class="brand__name">Tallow Crest</div>
  </div>
</section>

<section class="card card--front">
  <div class="pattern-field" role="img" aria-label="Faint large brand decoration in soft grey"></div>

  <div class="holder">
    <h1 class="holder__name">Rupert Hazelby</h1>
    <p class="holder__title">Director</p>
  </div>

  <ul class="contacts">
    <li class="contact">
      <svg class="contact__icon" viewBox="0 0 46 36" aria-hidden="true">
        <rect x="2" y="1" width="18" height="33" rx="3" fill="none" stroke="var(--icon-grey)" stroke-width="1.6"/>
        <rect x="5" y="6" width="12" height="21" fill="none" stroke="var(--icon-grey)" stroke-width="1"/>
        <circle cx="11" cy="30.5" r="1.5" fill="var(--icon-grey)"/>
      </svg>
      <span class="contact__text">0427 915203</span>
    </li>
    <li class="contact">
      <svg class="contact__icon" viewBox="0 0 46 36" aria-hidden="true">
        <rect x="1" y="10" width="32" height="18" fill="none" stroke="var(--icon-grey)" stroke-width="1.6"/>
        <polyline points="1,10 17,21 33,10" fill="none" stroke="var(--icon-grey)" stroke-width="1.6"/>
      </svg>
      <span class="contact__text">rupert@tallowcrest.com.au</span>
    </li>
    <li class="contact">
      <svg class="contact__icon" viewBox="0 0 46 36" aria-hidden="true">
        <text x="0" y="16" font-family="Arimo, Arial, sans-serif" font-size="11" fill="var(--icon-grey)">www</text>
        <path d="M27 10 L27 30 L31 26 L34 33 L37 32 L34 25 L40 25 Z" fill="none" stroke="var(--icon-grey)" stroke-width="1.4" stroke-linejoin="round"/>
      </svg>
      <span class="contact__text">www.tallowcrest.com.au</span>
    </li>
  </ul>
</section>

</body>
</html>
```